Business card design needed

I would like a one sided black business card with the information provided above. Refer to my website www.brightvolleyracquets.com.au for an example of colors I have used for my site, would like to keep this consistent for my business cards also, I will upload my logo below.

I am a new small business that provides tennis customers with racquet re stringing, tennis strings and accessories.

Industry/Entity Type

Small Business

Contact Information for Business Card

Bright Volley Tennis

Owen Whitby
Managing Director

brightvolleyracquets@mailbox.example
www.brightvolleyracquets.com.au
0491 726 305

Racquet Restringing/Tennis Strings/Accessories

Requirements
Must have
• Must have my logo and card must be black

```html
<!DOCTYPE html>
<html lang="en">
<head>
<meta charset="utf-8">
<title>Bright Volley Tennis – Business Card</title>
<link rel="stylesheet" href="https://fonts.googleapis.com/css2?family=Open+Sans:ital,wght@0,400;0,700;1,700&display=swap">
<style>
  :root {
    --backdrop: #d9d6d2;
    --card-black: #000000;
    --lime: #b3d335;
    --blue: #1d5486;
    --white: #ffffff;
    --ink: #111111;
  }
  * { box-sizing: border-box; margin: 0; padding: 0; }
  html, body {
    width: 1200px;
    height: 750px;
    overflow: hidden;
    background: var(--backdrop);
    font-family: "Open Sans", Arial, sans-serif;
  }
  .card {
    position: absolute;
    left: 75px;
    top: 75px;
    width: 1050px;
    height: 600px;
    background: var(--card-black);
    border-radius: 34px;
    overflow: hidden;
  }
  .brand {
    position: absolute;
    left: 0;
    right: 0;
    top: 150px;
    display: flex;
    justify-content: center;
    align-items: center;
    gap: 22px;
  }
  .brand-dot {
    width: 58px;
    height: 58px;
    border-radius: 50%;
    background: var(--lime);
  }
  .brand-name {
    color: var(--lime);
    font-weight: 700;
    font-size: 60px;
    line-height: 1;
  }
  .services {
    position: absolute;
    left: 0;
    right: 0;
    top: 320px;
    text-align: center;
    color: var(--white);
    font-size: 26px;
    line-height: 36px;
  }
  .services .bullet {
    display: inline-block;
    width: 8px;
    height: 8px;
    background: var(--white);
    vertical-align: middle;
    margin: 0 8px 4px 6px;
  }
  .contact-name {
    position: absolute;
    left: 0;
    right: 0;
    top: 436px;
    text-align: center;
    color: var(--lime);
    font-size: 26px;
    line-height: 40px;
  }
  .contact-name strong {
    font-size: 32px;
    font-weight: 700;
  }
  .contact-phone {
    position: absolute;
    left: 0;
    right: 0;
    top: 485px;
    text-align: center;
    color: var(--white);
    font-size: 26px;
    line-height: 34px;
  }
  .contact-phone em {
    font-weight: 700;
    font-style: italic;
  }
  .footer-band {
    position: absolute;
    left: 0;
    bottom: 0;
    width: 1050px;
    height: 64px;
  }
  .footer-band svg { position: absolute; inset: 0; }
  .footer-email,
  .footer-web {
    position: absolute;
    top: 0;
    height: 64px;
    line-height: 64px;
    font-size: 23px;
    text-align: center;
  }
  .footer-email {
    left: 0;
    width: 490px;
    color: var(--white);
  }
  .footer-email em { font-weight: 700; font-style: italic; }
  .footer-web {
    left: 510px;
    width: 540px;
    color: var(--ink);
  }
</style>
</head>
<body>
  <div class="card">
    <div class="brand">
      <span class="brand-dot"></span>
      <span class="brand-name">Bright Volley Tennis</span>
    </div>

    <p class="services">
      <span class="bullet"></span>Racquet Restringing<span class="bullet"></span>Tennis Strings<span class="bullet"></span>Accessories
    </p>

    <p class="contact-name"><strong>Owen Whitby,</strong> Managing Director</p>
    <p class="contact-phone"><em>phone</em> 0491 726 305</p>

    <div class="footer-band">
      <svg width="1050" height="64" viewBox="0 0 1050 64">
        <polygon points="0,0 462,0 502,64 0,64" fill="var(--blue)"/>
        <polygon points="482,0 1050,0 1050,64 524,64" fill="var(--lime)"/>
      </svg>
      <p class="footer-email"><em>e</em> brightvolleyracquets@mailbox.example</p>
      <p class="footer-web">www.brightvolleyracquets.com.au</p>
    </div>
  </div>
</body>
</html>
```